Stylish new business card needed!

Hello everyone! I am in need of a new business card design for an alarm company here in Hurricane WV. I have all fonts, color codes and logos provided for you use! We are a young company and like the style of a clean sleek looking business card. Would like it double sided, one side holding the logo and the other with your design!
Target Market(s)
The people that are looking for the newest tech for home automation and security
Industry/Entity Type
Alarm services; Home automation
Contact Information for Business Card
Name of person; position (Sales; Installer); Phone Number (555.418.7260); Employee cell Number; Website (www.GuardedByVelk.example); Employee Email; Double sided
Look and feel
Each slider illustrates characteristics of the customer's brand and the style your logo design should communicate.

```html
<!DOCTYPE html>
<html lang="en">
<head>
<meta charset="utf-8">
<title>Velk Business Card</title>
<link href="https://fonts.googleapis.com/css2?family=Arimo:wght@400;700&family=Archivo+Black&display=swap" rel="stylesheet">
<style>
  :root {
    --orange: #f59053;
    --grey: #9b9b9b;
    --white: #ffffff;
    --stage: #2a2a2a;
  }
  * { margin: 0; padding: 0; box-sizing: border-box; }
  html, body { width: 1200px; height: 880px; overflow: hidden; }
  body {
    background: var(--stage);
    font-family: "Arimo", Arial, sans-serif;
    position: relative;
  }
  .card {
    position: absolute;
    left: 320px;
    width: 560px;
    height: 320px;
    overflow: hidden;
  }
  .card--front { top: 100px; background: var(--orange); }
  .card--back { top: 460px; background: var(--white); }

  .front-brand {
    position: absolute;
    left: 0; right: 0; top: 92px;
    text-align: center;
    color: var(--white);
  }
  .front-brand__name {
    font-size: 104px;
    font-weight: 400;
    letter-spacing: 6px;
    line-height: 1;
  }
  .front-brand__tagline {
    margin-top: 12px;
    font-family: "Archivo Black", "Arial Black", sans-serif;
    font-size: 11px;
    letter-spacing: 1.5px;
  }

  .back-waves { position: absolute; inset: 0; }

  .back-brand {
    position: absolute;
    left: 48px; top: 104px;
    display: flex;
    align-items: center;
    gap: 12px;
  }
  .back-brand__mark {
    width: 22px; height: 22px;
    border-radius: 50%;
    background: var(--orange);
  }
  .back-brand__name {
    font-size: 60px;
    font-weight: 400;
    letter-spacing: 3px;
    color: var(--grey);
    line-height: 1;
  }

  .contact {
    position: absolute;
    right: 20px; top: 108px;
    text-align: right;
    color: var(--white);
  }
  .contact__name {
    font-family: "Archivo Black", "Arial Black", sans-serif;
    font-size: 15px;
    letter-spacing: 0.5px;
    line-height: 20px;
  }
  .contact__role {
    font-size: 13px;
    line-height: 18px;
    margin-right: 22px;
  }
  .contact__list { list-style: none; margin-top: 16px; }
  .contact__item {
    display: flex;
    justify-content: flex-end;
    align-items: center;
    gap: 8px;
    font-size: 13px;
    line-height: 20px;
  }
  .contact__item svg { width: 13px; height: 13px; flex: none; }
</style>
</head>
<body>

<section class="card card--front" aria-label="Card front">
  <div class="front-brand">
    <div class="front-brand__name">VELK</div>
    <div class="front-brand__tagline">AUTOMATION AND SECURITY SERVICES</div>
  </div>
</section>

<section class="card card--back" aria-label="Card back">
  <svg class="back-waves" viewBox="0 0 560 320" aria-hidden="true">
    <path d="M560,45 C460,48 395,60 360,105 C325,150 310,210 260,250 C200,295 100,305 0,300"
          fill="none" stroke="var(--orange)" stroke-width="5" transform="translate(-26,-22)"/>
    <path d="M560,45 C460,48 395,60 360,105 C325,150 310,210 260,250 C200,295 100,305 0,300"
          fill="none" stroke="var(--grey)" stroke-width="10" transform="translate(-12,-11)"/>
    <path d="M560,45 C460,48 395,60 360,105 C325,150 310,210 260,250 C200,295 100,305 0,300 L0,320 L560,320 Z"
          fill="var(--orange)"/>
  </svg>

  <div class="back-brand">
    <span class="back-brand__name">VELK</span>
    <span class="back-brand__mark"></span>
  </div>

  <div class="contact">
    <div class="contact__name">DANA WHITCOMBE</div>
    <div class="contact__role">Sales; Installer</div>
    <ul class="contact__list">
      <li class="contact__item">555.418.7260
        <svg viewBox="0 0 16 16"><path d="M3 2h3l1 3-2 1.5a9 9 0 0 0 4.5 4.5L11 9l3 1v3a1 1 0 0 1-1 1A12 12 0 0 1 2 3a1 1 0 0 1 1-1z" fill="var(--white)"/></svg>
      </li>
      <li class="contact__item">555.418.7264
        <svg viewBox="0 0 16 16"><rect x="4" y="1" width="8" height="14" rx="1.5" fill="none" stroke="var(--white)" stroke-width="1.5"/><circle cx="8" cy="12.5" r="0.9" fill="var(--white)"/></svg>
      </li>
      <li class="contact__item">info@GuardedByVelk.example
        <svg viewBox="0 0 16 16"><rect x="1" y="3" width="14" height="10" fill="var(--white)"/><path d="M1 3l7 6 7-6" fill="none" stroke="var(--orange)" stroke-width="1.2"/></svg>
      </li>
      <li class="contact__item">www.GuardedByVelk.example
        <svg viewBox="0 0 16 16"><circle cx="8" cy="8" r="6.5" fill="var(--white)"/><path d="M1.5 8h13M8 1.5c-3 3.5-3 9.5 0 13M8 1.5c3 3.5 3 9.5 0 13" fill="none" stroke="var(--orange)" stroke-width="1"/></svg>
      </li>
    </ul>
  </div>
</section>

</body>
</html>
```